Business Card Design Project

Business Card
We are rebranding with a new logo
Industry/Entity Type
Business
Contact Information for Business Card
Dennis Morvale +61 487215963 dennis@quorv.com.au P.O. Box 872 Fernlow QLD 4309
Requirements
Must have
- Logo

```html
<!DOCTYPE html>
<html lang="en">
<head>
<meta charset="utf-8">
<title>Quorv International – Business Card</title>
<link href="https://fonts.googleapis.com/css2?family=Roboto+Condensed:wght@700&family=Roboto:wght@400;500&display=swap" rel="stylesheet">
<style>
  :root {
    --backdrop: #2a2a2a;
    --card-white: #f3f3f3;
    --brand-blue: #1a86c2;
    --band-deep: #0d4f72;
    --band-mid: #11729f;
    --band-light: #0aa0dc;
    --accent-orange: #ef8a1e;
    --ink-light: #ffffff;
  }
  html, body {
    margin: 0;
    padding: 0;
    width: 1200px;
    height: 960px;
    overflow: hidden;
    background: var(--backdrop);
  }
  .card {
    position: absolute;
    left: 223px;
    top: 265px;
    width: 754px;
    height: 430px;
    border-radius: 20px;
    overflow: hidden;
    background: var(--card-white);
    font-family: "Roboto", Arial, sans-serif;
  }
  .card__band {
    position: absolute;
    inset: 0;
    width: 754px;
    height: 430px;
  }
  .card__name {
    position: absolute;
    left: 43px;
    top: 52px;
    margin: 0;
    font-family: "Roboto Condensed", "Arial Narrow", sans-serif;
    font-weight: 700;
    font-size: 26px;
    letter-spacing: 0.2px;
    color: var(--brand-blue);
    text-transform: uppercase;
  }
  .brand {
    position: absolute;
    right: 48px;
    top: 62px;
    text-align: right;
    font-family: "Roboto", Arial, sans-serif;
    font-weight: 500;
    color: var(--brand-blue);
  }
  .brand__name {
    display: block;
    font-size: 64px;
    line-height: 1;
  }
  .brand__tag {
    display: block;
    margin-top: 14px;
    font-size: 20px;
    letter-spacing: 3px;
  }
  .contact {
    position: absolute;
    left: 38px;
    top: 326px;
    margin: 0;
    padding: 0;
    list-style: none;
    color: var(--ink-light);
    font-size: 17px;
    line-height: 24px;
  }
  .contact__item {
    display: flex;
    align-items: center;
  }
  .contact__icon {
    width: 18px;
    height: 18px;
    margin-right: 10px;
    fill: var(--ink-light);
  }
  .address {
    position: absolute;
    right: 38px;
    top: 350px;
    margin: 0;
    text-align: right;
    color: var(--ink-light);
    font-style: normal;
    font-size: 17px;
    line-height: 24px;
  }
</style>
</head>
<body>
<div class="card">
  <svg class="card__band" viewBox="0 0 754 430" aria-hidden="true">
    <defs>
      <radialGradient id="bandGlow" cx="400" cy="330" r="420" gradientUnits="userSpaceOnUse">
        <stop offset="0" stop-color="var(--band-light)"/>
        <stop offset="0.55" stop-color="var(--band-mid)"/>
        <stop offset="1" stop-color="var(--band-deep)"/>
      </radialGradient>
    </defs>
    <path d="M380,312 C540,306 680,278 754,250 L754,282 C680,300 560,312 420,314 Z" fill="var(--accent-orange)"/>
    <path d="M0,218 C170,262 360,312 470,313 C600,314 700,294 754,282 L754,430 L0,430 Z" fill="var(--band-deep)"/>
    <path d="M0,230 C170,272 360,318 470,318 C600,318 700,298 754,288 L754,430 L0,430 Z" fill="url(#bandGlow)"/>
    <path d="M0,218 C170,262 360,312 470,313 C600,314 700,294 754,282" fill="none" stroke="#ffffff" stroke-width="2"/>
  </svg>

  <h1 class="card__name">Dennis Morvale</h1>

  <div class="brand">
    <span class="brand__name">Quorv</span>
    <span class="brand__tag">INTERNATIONAL</span>
  </div>

  <ul class="contact">
    <li class="contact__item">
      <svg class="contact__icon" viewBox="0 0 24 24" aria-hidden="true"><path d="M6.6 10.8a15.1 15.1 0 0 0 6.6 6.6l2.2-2.2c.3-.3.7-.4 1-.2 1.1.4 2.3.6 3.6.6.6 0 1 .4 1 1V20c0 .6-.4 1-1 1A17 17 0 0 1 3 4c0-.6.4-1 1-1h3.5c.6 0 1 .4 1 1 0 1.3.2 2.5.6 3.6.1.3 0 .7-.2 1z"/></svg>
      +61 487215963
    </li>
    <li class="contact__item">
      <svg class="contact__icon" viewBox="0 0 24 24" aria-hidden="true"><path d="M3 6h18v12H3z M3 6l9 7 9-7" fill="none" stroke="#fff" stroke-width="2"/></svg>
      dennis@quorv.com.au
    </li>
    <li class="contact__item">
      <svg class="contact__icon" viewBox="0 0 24 24" aria-hidden="true"><circle cx="12" cy="12" r="9" fill="none" stroke="#fff" stroke-width="2"/><path d="M3 12h18M12 3c3 3 3 15 0 18M12 3c-3 3-3 15 0 18" fill="none" stroke="#fff" stroke-width="1.6"/></svg>
      www.quorv.com.au
    </li>
  </ul>

  <address class="address">P.O. Box 872<br>Fernlow QLD 4309</address>
</div>
</body>
</html>
```